Tolvik Commercial Cleaning is lookong for a new business card design.

A fresh new design that's professional and stylish. We need a serious upgrade to our business cards. I have included pictures of our existing ones. Our clients include professional individuals and business owners. We woupdblike something professional and upbeat. Please have fun and see what you come uo with.

Target Market(s)

Property managers, business owners, facility managers and other similar professionals

Industry/Entity Type

Janitorial

Contact Information for Business Card

Name, cell, office number, email, web address

Font styles to use
Sans Serif

Colors

Designer to choose colors to be used in the design.

Requirements
Must have
• please use the green color in our logo
Nice to have
• Bar code
Should not have
• Address

```html
<!DOCTYPE html>
<html lang="en">
<head>
<meta charset="utf-8">
<title>Tolvik Commercial Cleaning — Business Card</title>
<link rel="stylesheet" href="https://fonts.googleapis.com/css2?family=Montserrat:wght@400;500;600;700&display=swap">
<style>
  :root {
    --backdrop: #e9e4dc;
    --card-white: #ffffff;
    --brand-green: #41ad59;
    --deep-green: #2f8f46;
    --text-dark: #333333;
    --card-shadow: rgba(0, 0, 0, 0.35);
  }
  * { box-sizing: border-box; margin: 0; padding: 0; }
  html, body {
    width: 900px;
    height: 1200px;
    overflow: hidden;
  }
  body {
    position: relative;
    background: var(--backdrop);
    font-family: "Montserrat", Arial, sans-serif;
  }
  .card {
    position: absolute;
    left: 80px;
    width: 742px;
    height: 440px;
    border-radius: 40px;
    box-shadow: 4px 6px 10px var(--card-shadow);
  }
  .card-front { top: 132px; background: var(--card-white); }
  .card-back  { top: 638px; background: var(--brand-green); }

  .wordmark {
    position: absolute;
    text-align: center;
    font-weight: 600;
    line-height: 1;
  }
  .card-front .wordmark {
    left: 50px;
    width: 320px;
    top: 168px;
    color: var(--brand-green);
  }
  .wordmark-name { display: block; font-size: 78px; letter-spacing: 1px; }
  .wordmark-tag  { display: block; font-size: 21px; margin-top: 14px; }

  .divider {
    position: absolute;
    left: 392px;
    top: 164px;
    width: 2px;
    height: 136px;
    background: var(--brand-green);
  }

  .contact {
    position: absolute;
    left: 437px;
    top: 162px;
    color: var(--text-dark);
  }
  .contact-name {
    font-size: 25px;
    font-weight: 600;
    color: var(--brand-green);
  }
  .contact-role {
    font-size: 15px;
    margin-top: 3px;
    margin-bottom: 20px;
  }
  .contact-line {
    display: flex;
    align-items: center;
    gap: 10px;
    font-size: 15.5px;
    height: 22px;
  }
  .contact-line svg { width: 14px; height: 14px; flex: none; }

  .card-back .wordmark {
    left: 0;
    width: 742px;
    top: 130px;
    color: var(--deep-green);
  }
  .card-back .wordmark-name { font-size: 118px; }
  .card-back .wordmark-tag  { font-size: 30px; margin-top: 22px; }
</style>
</head>
<body>
  <section class="card card-front" aria-label="Business card front">
    <div class="wordmark">
      <span class="wordmark-name">Tolvik</span>
      <span class="wordmark-tag">Commercial Cleaning</span>
    </div>
    <div class="divider"></div>
    <div class="contact">
      <p class="contact-name">Mara Ellison</p>
      <p class="contact-role">CEO &amp; Founder</p>
      <p class="contact-line">
        <svg viewBox="0 0 14 14" aria-hidden="true"><path fill="#41ad59" d="M1 5c0-2 2-3 6-3s6 1 6 3v1h-3V5H4v1H1zM3 7h8l1 5H2z"/><circle cx="7" cy="9.5" r="1.4" fill="#fff"/></svg>
        (37) 555-0182
      </p>
      <p class="contact-line">
        <svg viewBox="0 0 14 14" aria-hidden="true"><rect x="1" y="3" width="12" height="8" fill="#41ad59"/><path d="M1 3l6 5 6-5" fill="none" stroke="#fff" stroke-width="1.2"/></svg>
        mara@tolvikcleaning.com
      </p>
      <p class="contact-line">
        <svg viewBox="0 0 14 14" aria-hidden="true"><circle cx="7" cy="7" r="6" fill="#41ad59"/><path d="M1 7h12M7 1c-2.5 3-2.5 9 0 12M7 1c2.5 3 2.5 9 0 12" fill="none" stroke="#fff" stroke-width="0.9"/></svg>
        www.tolvikcleaning.com
      </p>
    </div>
  </section>

  <section class="card card-back" aria-label="Business card back">
    <div class="wordmark">
      <span class="wordmark-name">Tolvik</span>
      <span class="wordmark-tag">Commercial Cleaning</span>
    </div>
  </section>
</body>
</html>
```